Brell Stone Company Business Cards

Front and Back Business Card - logo and text setup - cool design. I need workable photoshop or illustrator files so I can setup each employee card with design that is created
Updates

Hi everyone, thank you for the great entries. Please no more white and blue cards - there are so many already - black and silver only now please. thanks!

Target Market(s)

Construction Industry - Facility Managers

Industry/Entity Type

Construction

Contact Information for Business Card

I really like contemporary simplistic looks - clean neat....not opposed to seeing some black backrounds

Requirements
Must have
• Logo/website address with design on front only - www.brellstone-example.com (logo attached)
• Back:
• Name/Title/Company Address/Phone/email address
Nice to have
• Cool design
Should not have
• Nothing gimmicky like Fire or Water - since we are a Fire Protection company - it has all been done

```html
<!DOCTYPE html>
<html lang="en">
<head>
<meta charset="utf-8">
<title>Brell Stone Company Business Cards</title>
<link rel="stylesheet" href="https://fonts.googleapis.com/css2?family=Open+Sans:wght@400;600;700;800&display=swap">
<style>
  :root {
    --backdrop: #c9cbcd;
    --card-black: #000000;
    --brand-blue: #0623a0;
    --brand-red: #ff2121;
    --text-white: #ffffff;
    --mark-grey: #7d7d7d;
  }
  * { margin: 0; padding: 0; box-sizing: border-box; }
  html, body {
    width: 1200px;
    height: 1193px;
    overflow: hidden;
    background: var(--backdrop);
    font-family: "Open Sans", Arial, sans-serif;
  }
  .card {
    position: absolute;
    left: 120px;
    width: 960px;
    height: 520px;
    border-radius: 44px;
    overflow: hidden;
    background: var(--card-black);
    color: var(--text-white);
  }
  .card-front { top: 60px; }
  .card-back { top: 613px; }

  .front-shapes { position: absolute; inset: 0; }

  .company-name {
    position: absolute;
    left: 70px;
    top: 78px;
    font-size: 64px;
    font-weight: 800;
    letter-spacing: -1px;
    color: var(--brand-red);
  }
  .person { position: absolute; left: 78px; top: 262px; }
  .person-name { font-size: 38px; font-weight: 700; line-height: 1.2; }
  .person-title { font-size: 34px; font-weight: 400; line-height: 1.3; }

  .contact-list {
    position: absolute;
    right: 48px;
    top: 296px;
    list-style: none;
    text-align: right;
  }
  .contact-item {
    display: flex;
    justify-content: flex-end;
    align-items: center;
    gap: 16px;
    font-size: 22px;
    line-height: 40px;
  }
  .contact-icon { width: 24px; height: 24px; fill: none; stroke: var(--text-white); stroke-width: 2; }
  .contact-icon.solid { fill: var(--text-white); stroke: none; }

  .address {
    position: absolute;
    right: 48px;
    bottom: 22px;
    font-size: 22px;
    font-weight: 400;
  }

  .back-lockup {
    position: absolute;
    inset: 0;
    display: flex;
    flex-direction: column;
    align-items: center;
    justify-content: center;
    gap: 28px;
  }
  .back-company {
    font-size: 76px;
    font-weight: 800;
    letter-spacing: -1px;
    color: var(--mark-grey);
  }
  .back-web {
    font-size: 30px;
    font-weight: 400;
    letter-spacing: 6px;
  }
</style>
</head>
<body>

<section class="card card-front">
  <svg class="front-shapes" viewBox="0 0 960 520" width="960" height="520" aria-hidden="true">
    <path fill="var(--brand-blue)" d="M0 470 C 250 520 600 400 960 0 L960 520 L0 520 Z"/>
    <path fill="var(--brand-red)" d="M0 410 C 150 470 300 460 400 400 C 300 485 150 500 0 450 Z"/>
  </svg>

  <div class="company-name">Brell Stone Company</div>

  <div class="person">
    <div class="person-name">Dana Whitfield</div>
    <div class="person-title">President</div>
  </div>

  <ul class="contact-list">
    <li class="contact-item">(555) 014-2290
      <svg class="contact-icon solid" viewBox="0 0 24 24"><path d="M6.6 10.8a15 15 0 0 0 6.6 6.6l2.2-2.2a1 1 0 0 1 1-.25 11.4 11.4 0 0 0 3.6.57 1 1 0 0 1 1 1V20a1 1 0 0 1-1 1A17 17 0 0 1 3 4a1 1 0 0 1 1-1h3.5a1 1 0 0 1 1 1c0 1.25.2 2.45.57 3.57a1 1 0 0 1-.25 1z"/></svg>
    </li>
    <li class="contact-item">info@brellstone-example.com
      <svg class="contact-icon" viewBox="0 0 24 24"><rect x="2" y="5" width="20" height="14"/><path d="M2 5l10 8 10-8M2 19l7-7M22 19l-7-7"/></svg>
    </li>
    <li class="contact-item">www.brellstone-example.com
      <svg class="contact-icon" viewBox="0 0 24 24"><circle cx="12" cy="12" r="10"/><ellipse cx="12" cy="12" rx="4.5" ry="10"/><path d="M2 12h20M4 7h16M4 17h16"/></svg>
    </li>
  </ul>

  <div class="address">48 Harbor Lane, Milford Point, NY 10000</div>
</section>

<section class="card card-back">
  <div class="back-lockup">
    <div class="back-company">Brell Stone Company</div>
    <div class="back-web">www.brellstone-example.com</div>
  </div>
</section>

</body>
</html>
```